Design a Job Application & CV

I need a design for upcoming job applications that includes a cv. It needs to look as elegant and modern as possible as the application will be send mainly to large corporations and strategy consultancies. I have attached an application that I like for your consideration. One of the more difficult requirements is that it needs to be editable in ms office word for mac/windows.
As stated only the design is part of this project. I will fill in my content later on.
Reason: Dear Designers,
I am going to increase the budget as well as extending the deadline. I am hoping that you can improve upon the design that I have provided in the brief. If you have questions please let me know.
Dear Designers,
Target Market(s)
Human Resources Managers, Senior Consultants and Executives of larger firms
Industry/Entity Type
Office
Requirements
Must have
- 4 Pages including( a cover page, a coverletter page, 2 pages cv)
It should be easy to edit and should be readable by word for mac, i.e. in the *.docx format.
Here is an example of what I like:
http://www.torvenmald.example/applicationexample.pdf
http://www.torvenmald.example/applicationExample.docx
colors that I like are blue, grey, black, white
Nice to have
- icons to indicate sections
Should not have
- invasive cliparts

```html
<!DOCTYPE html>
<html lang="en">
<head>
<meta charset="utf-8">
<title>John Doe – Application &amp; CV</title>
<link rel="stylesheet" href="https://fonts.googleapis.com/css2?family=Open+Sans:wght@300;400;600&family=Didact+Gothic&display=swap">
<style>
  :root {
    --backdrop: #5b5b5b;
    --backdrop-dark: #4e4e4e;
    --charcoal: #3b3b3b;
    --footer: #1e1e1e;
    --footer-light: #2c2c2c;
    --accent: #12a9ec;
    --heading-blue: #2673c4;
    --ink: #555555;
    --ink-soft: #707070;
    --paper: #ffffff;
  }
  * { margin: 0; padding: 0; box-sizing: border-box; }
  html, body { width: 1200px; height: 821px; overflow: hidden; }
  body {
    position: relative;
    background: linear-gradient(180deg, var(--backdrop), var(--backdrop-dark));
    font-family: "Didact Gothic", "Century Gothic", sans-serif;
    color: var(--ink);
  }

  .page {
    position: absolute;
    top: 0;
    height: 821px;
    background: var(--paper);
    overflow: hidden;
  }
  .page--cv { left: 25px; width: 561px; }
  .page--cv-continued { left: 602px; width: 571px; }

  .page__header {
    position: absolute;
    left: 0; top: 0; right: 0;
    height: 145px;
  }
  .page__rule {
    position: absolute;
    left: 0; right: 0;
    top: 145px;
    height: 14px;
  }
  .page--cv .page__header { background: var(--charcoal); }
  .page--cv .page__rule { background: var(--accent); }
  .page--cv-continued .page__header { background: var(--accent); }
  .page--cv-continued .page__rule { background: var(--charcoal); }

  .page__footer {
    position: absolute;
    left: 0; right: 0; bottom: 0;
    height: 72px;
    background: linear-gradient(180deg, var(--footer-light), var(--footer));
  }

  .name {
    position: absolute;
    left: 38px;
    top: 54px;
    font-family: "Open Sans", "Segoe UI", sans-serif;
    font-weight: 300;
    font-size: 66px;
    line-height: 1;
    letter-spacing: -1px;
    white-space: nowrap;
  }
  .page--cv .name__first { color: var(--paper); }
  .page--cv .name__last { color: var(--accent); }
  .page--cv-continued .name { left: 52px; top: 62px; }
  .page--cv-continued .name__first { color: var(--charcoal); }
  .page--cv-continued .name__last { color: var(--paper); }

  .contact {
    position: absolute;
    top: 29px;
    font-family: "Open Sans", "Segoe UI", sans-serif;
    font-size: 14px;
    line-height: 16px;
    color: var(--paper);
  }
  .page--cv .contact { left: 279px; }
  .page--cv-continued .contact { left: 288px; }

  .section {
    position: absolute;
    left: 0; right: 0;
  }
  .section__title {
    position: absolute;
    width: 215px;
    text-align: right;
    font-family: "Open Sans", "Segoe UI", sans-serif;
    font-weight: 600;
    font-size: 18px;
    line-height: 22px;
    color: var(--heading-blue);
  }
  .page--cv-continued .section__title { width: 198px; }

  .summary {
    position: absolute;
    left: 221px;
    top: 2px;
    width: 300px;
    font-size: 12px;
    line-height: 16px;
    color: var(--ink);
  }
  .page--cv-continued .summary { left: 209px; top: 6px; }

  .facts {
    position: absolute;
    top: 30px;
    width: 211px;
    text-align: right;
    list-style: none;
    font-size: 14px;
    line-height: 18px;
    color: var(--ink-soft);
  }

  .entries {
    position: absolute;
    top: 27px;
    left: 0; right: 0;
  }
  .entry {
    display: grid;
    grid-template-columns: 211px 1fr;
    column-gap: 10px;
    font-size: 11px;
    line-height: 14.5px;
    color: var(--ink-soft);
  }
  .page--cv-continued .entry { grid-template-columns: 197px 1fr; }
  .entry__role { text-align: right; }
  .entry__role span { display: block; }
  .entry__role .caps { font-size: 10px; text-transform: uppercase; }
  .entry__detail span { display: block; }
  .entry__school { font-size: 13px; letter-spacing: 0.5px; text-transform: uppercase; }
  .entry--degree .entry__role { font-size: 14px; line-height: 18px; }
  .entry--degree .entry__detail { line-height: 14px; }
</style>
</head>
<body>

<section class="page page--cv">
  <header class="page__header">
    <h1 class="name"><span class="name__first">John</span> <span class="name__last">Doe</span></h1>
    <address class="contact">
      1234 Street, Town, City, Country, Zip Code<br>
      Contact Number<br>
      Email Address
    </address>
  </header>
  <div class="page__rule"></div>

  <section class="section" style="top:187px">
    <h2 class="section__title">Objective</h2>
    <p class="summary">Lorem ipsum dolor sit amet, consectetur adipiscing elit. Nullam pulvinar volutpat tempor. Lorem ipsum dolor sit amet, consectetur adipiscing elit.</p>
  </section>

  <section class="section" style="top:271px">
    <h2 class="section__title">Personal Info</h2>
    <ul class="facts">
      <li>Nationality</li>
      <li>Birthday</li>
      <li>Birthplace</li>
    </ul>
  </section>

  <section class="section" style="top:381px">
    <h2 class="section__title">Employment</h2>
    <div class="entries">
      <div class="entry">
        <div class="entry__role"><span class="caps">Job Position</span><span>(Employer)</span></div>
        <div class="entry__detail"><span>2000-2009</span><span>(Address)</span><span>(Description)</span></div>
      </div>
      <div class="entry">
        <div class="entry__role"><span class="caps">Job Position</span><span>(Employer)</span></div>
        <div class="entry__detail"><span>2000-2009</span><span>(Address)</span><span>(Description)</span></div>
      </div>
    </div>
  </section>

  <section class="section" style="top:520px">
    <h2 class="section__title">Education</h2>
    <div class="entries">
      <div class="entry entry--degree">
        <div class="entry__role"><span>AB Mass Communications</span></div>
        <div class="entry__detail"><span>2004-2008</span><span class="entry__school">Harrowgate University</span><span>Adress</span><span>(Description)</span></div>
      </div>
    </div>
  </section>

  <footer class="page__footer"></footer>
</section>

<section class="page page--cv-continued">
  <header class="page__header">
    <h1 class="name"><span class="name__first">John</span> <span class="name__last">Doe</span></h1>
    <address class="contact">
      1234 Street, Town, City, Country, Zip Code<br>
      Contact Number<br>
      Email Address
    </address>
  </header>
  <div class="page__rule"></div>

  <section class="section" style="top:180px">
    <h2 class="section__title">Objective</h2>
    <p class="summary">Lorem ipsum dolor sit amet, consectetur adipiscing elit. Nullam pulvinar volutpat tempor. Lorem ipsum dolor sit amet, consectetur adipiscing elit.</p>
  </section>

  <section class="section" style="top:276px">
    <h2 class="section__title">Employment</h2>
    <div class="entries">
      <div class="entry">
        <div class="entry__role"><span class="caps">Job Position</span><span>(Employer)</span></div>
        <div class="entry__detail"><span>2000-2009</span><span>(Address)</span><span>(Description)</span></div>
      </div>
      <div class="entry">
        <div class="entry__role"><span class="caps">Job Position</span><span>(Employer)</span></div>
        <div class="entry__detail"><span>2000-2009</span><span>(Address)</span><span>(Description)</span></div>
      </div>
    </div>
  </section>

  <section class="section" style="top:393px">
    <h2 class="section__title">Employment</h2>
    <div class="entries">
      <div class="entry">
        <div class="entry__role"><span class="caps">Job Position</span><span>(Employer)</span></div>
        <div class="entry__detail"><span>2000-2009</span><span>(Address)</span><span>(Description)</span></div>
      </div>
      <div class="entry">
        <div class="entry__role"><span class="caps">Job Position</span><span>(Employer)</span></div>
        <div class="entry__detail"><span>2000-2009</span><span>(Address)</span><span>(Description)</span></div>
      </div>
    </div>
  </section>

  <section class="section" style="top:509px">
    <h2 class="section__title">Employment</h2>
    <div class="entries">
      <div class="entry">
        <div class="entry__role"><span class="caps">Job Position</span><span>(Employer)</span></div>
        <div class="entry__detail"><span>2000-2009</span><span>(Address)</span><span>(Description)</span></div>
      </div>
      <div class="entry">
        <div class="entry__role"><span class="caps">Job Position</span><span>(Employer)</span></div>
        <div class="entry__detail"><span>2000-2009</span><span>(Address)</span><span>(Description)</span></div>
      </div>
    </div>
  </section>

  <footer class="page__footer"></footer>
</section>

</body>
</html>
```